Business card design needed to incorporate existing logo

We need a business card for a new modern Accounting & Business Solutions company call TelmaNord Partners.com.au servicing all of Australia.
My tagline is Steady Ledger Answers... that deliver.

We specialise in Cloud Accounting and this is our primary focus. We also provide tax representation, debt recovery, computer, tablet and smart phone sales.

I would like a design that uses my corporate, trustworthy colours of blue/white, black/grey however am open to suggestion. I have attached my logo to go on the card somewhere,of which you will see the colour scheme.

I am after a card that STANDS OUT, somewhere between it not being too busy and not being a baron waste of space.

A 'cloud' incorporated in the design may work well, up to your artistic judgement. I know what I like when I see it; it is harder to put into words!

Excited to see your ideas!
I have added my logo predominately (blue/white) and for additional opportunity have added my reverse logo (darker one). I have used the blue/white on my website and letterhead. I will be using both on my vehicle signage.

Target Market(s)

Tradesmen and small-medium businesses of all descriptions Australia-wide

Industry/Entity Type

Debt

Contact Information for Business Card

Doug Hallett
Principal (optional)
TelmaNord Partners.com.au
Steady Ledger Answers... that deliver

P: 1800 493 518
M: 0412 658 071 (optional)
W: www.telmanordpartners.com.au
E: admin@telmanordpartners.com.au

Logo Text

Steady Ledger Answers... that deliver!

Logo styles of interest
Wordmark Logo
Requirements
Must have
• Must look professional and of high quality not cheap.

My logo and my tagline 'Steady Ledger Answers... that deliver'.

I have my colourscheme in mind as per my attached logo, however am open to suggestion. I want to see what you can create that I would not have thought of.

Modern, innovative.
Something I won't look at and think, 'I could have done that myself'.

Must be able to be printed on Prinvo 300gm premium cards and the artwork provided to me.
Nice to have
• Title of Principal is optional depending on space and judement call of look/fee.
M: (mobile) number is also optional as above.

Somthing cloud related given the Cloud Accounting aspect may be relevant. I leave it to your artistic design and judgement.
Should not have
• Must not look cheap.

```html
<!DOCTYPE html>
<html lang="en">
<head>
<meta charset="utf-8">
<title>TelmaNord Partners – Business Card</title>
<link rel="stylesheet" href="https://fonts.googleapis.com/css2?family=Open+Sans:wght@400;600;700&display=swap">
<style>
  :root {
    --backdrop: #1c2a5c;
    --card: #ffffff;
    --brand-blue: #1f7fc4;
    --brand-navy: #2b3a7a;
    --ink: #2b2b2b;
    --muted: #5a5a5a;
    --rule: #c9c9c9;
    --pill: #a9a9a9;
    --globe-light: #4aa3dc;
    --globe-deep: #1565ad;
  }
  * { box-sizing: border-box; margin: 0; padding: 0; }
  html, body {
    width: 1200px; height: 675px; overflow: hidden;
    background: var(--backdrop);
    font-family: "Open Sans", Arial, sans-serif;
  }
  .business-card {
    position: absolute; left: 150px; top: 62px;
    width: 900px; height: 550px;
    background: var(--card);
    overflow: hidden;
    box-shadow: 0 18px 40px rgba(0,0,0,.35);
  }
  .feature-art {
    position: absolute; right: 0; top: 0;
    width: 400px; height: 240px;
    background: radial-gradient(ellipse at 70% 35%, var(--globe-light) 0%, var(--globe-deep) 55%, rgba(21,101,173,0.15) 85%, rgba(255,255,255,0) 100%);
    border-bottom-left-radius: 200px;
  }
  .brand {
    position: absolute; left: 60px; top: 150px;
    width: 380px;
  }
  .brand-name {
    display: flex; align-items: center; gap: 12px;
    font-size: 34px; font-weight: 400; color: var(--brand-blue);
    line-height: 40px;
    letter-spacing: 0.5px;
  }
  .brand-dot {
    width: 20px; height: 20px; border-radius: 50%;
    background: var(--brand-navy);
    flex: none;
  }
  .tagline-pill {
    margin-top: 10px;
    display: inline-block;
    background: var(--pill);
    color: #fff;
    font-size: 12px; font-weight: 600;
    letter-spacing: 0.6px;
    text-transform: uppercase;
    padding: 4px 18px;
    border-radius: 12px;
    white-space: nowrap;
  }
  .web-contacts {
    position: absolute; right: 60px; top: 272px;
    text-align: right;
    font-size: 16px; color: var(--muted); line-height: 24px;
  }
  .web-contacts li { list-style: none; display: flex; justify-content: flex-end; align-items: center; gap: 8px; }
  .contact-icon { width: 14px; height: 14px; fill: var(--brand-blue); flex: none; }
  .divider-right {
    position: absolute; left: 480px; right: 50px; top: 332px;
    height: 1px; background: var(--rule);
  }
  .person {
    position: absolute; left: 60px; top: 362px;
  }
  .person-name { font-size: 24px; font-weight: 700; color: var(--brand-blue); line-height: 28px; }
  .person-title { font-size: 21px; font-weight: 400; color: var(--ink); line-height: 26px; }
  .divider-left {
    position: absolute; left: 60px; top: 428px;
    width: 260px; height: 1px; background: var(--rule);
  }
  .phone-list {
    position: absolute; left: 60px; top: 440px;
    font-size: 17px; color: var(--ink); line-height: 24px;
  }
  .phone-list li { list-style: none; display: flex; align-items: center; gap: 8px; }
</style>
</head>
<body>
  <main class="business-card">
    <div class="feature-art" role="img" aria-label="Large globe artwork showing Australia in blue tones"></div>

    <header class="brand">
      <div class="brand-name"><span class="brand-dot"></span><span>TelmaNord<br>Partners.com.au</span></div>
      <div class="tagline-pill">Steady Ledger Answers... that deliver</div>
    </header>

    <ul class="web-contacts">
      <li>admin@telmanordpartners.com.au
        <svg class="contact-icon" viewBox="0 0 14 14" aria-hidden="true"><rect x="1" y="3" width="12" height="8" rx="1"/><path d="M1.5 3.5 7 8l5.5-4.5" stroke="#fff" stroke-width="1.2" fill="none"/></svg>
      </li>
      <li>www.telmanordpartners.com.au
        <svg class="contact-icon" viewBox="0 0 14 14" aria-hidden="true"><circle cx="7" cy="7" r="6"/><path d="M1 7h12M7 1c-3 3-3 9 0 12M7 1c3 3 3 9 0 12" stroke="#fff" stroke-width="1" fill="none"/></svg>
      </li>
    </ul>
    <div class="divider-right"></div>

    <section class="person">
      <h1 class="person-name">Doug Hallett</h1>
      <p class="person-title">Principal</p>
    </section>
    <div class="divider-left"></div>

    <ul class="phone-list">
      <li>
        <svg class="contact-icon" viewBox="0 0 14 14" aria-hidden="true"><path d="M1 5c0-2 2-3 6-3s6 1 6 3v1h-3V5H4v1H1z"/><rect x="3" y="7" width="8" height="5" rx="1"/></svg>
        1800 493 518
      </li>
      <li>
        <svg class="contact-icon" viewBox="0 0 14 14" aria-hidden="true"><rect x="3.5" y="1" width="7" height="12" rx="1.5"/><rect x="5" y="3" width="4" height="6" fill="#fff"/></svg>
        0412 658 071
      </li>
    </ul>
  </main>
</body>
</html>
```